Real Estate Media Company Business Card

’m looking for a modern, high-end, double-sided business card for:
Bright Harbor Studios LLC
(Real Estate Photography & Videography)
The design should feel clean, minimal, and premium, appealing to top real estate agents and brokers.
👉 Horizontal layout is preferred
👉 Vertical option is welcome but not required
⸻
Front Side (Main Information):
Include:
* Desmond Whitfield
* Bright Harbor Studios LLC
* Title (open to creative improvement)
* Phone Number
* Email
* Website
⸻
Services Section (VERY IMPORTANT):
This should be a key visual element, not an afterthought.
Services to Include:
* Cinematic Video
* Real Estate Photography
* Drone
* Social Media Reels
* Floor Plans
* Use clean, modern icons next to each service
* Icons should be simple, minimal, and consistent style (outline or thin line preferred)
* Option to place icons inside small circles (like reference)
Layout:
* Format services similar to a clean horizontal or grid-style list (like “example 2”)
* Keep spacing balanced and uncluttered
* Make this section visually appealing and easy to scan
⸻
Back Side:
* Keep it extremely minimal
* Only include the logo in a corner
* No additional text needed
⸻
Typography & Style:
* Modern, clean, slightly bold fonts (based on uploaded references)
* Strong hierarchy (name + services stand out most)
* Plenty of white/negative space
* Avoid clutter
⸻
Overall Feel:
* Luxury
* Modern
* Clean
* Confident
* High-end real estate branding
⸻
Notes for Designers:
* Simplicity is key
* Services section should feel polished and intentional
* This card should feel like something a top-producing real estate agent would keep
Target Market(s)
Real estate agent agents

```html
<!DOCTYPE html>
<html lang="en">
<head>
<meta charset="utf-8">
<title>Bright Harbor Studios – Business Card</title>
<link href="https://fonts.googleapis.com/css2?family=Lato:wght@400;700&display=swap" rel="stylesheet">
<style>
  :root {
    --canvas: #e9e9e9;
    --card-light: #ffffff;
    --card-dark: #232323;
    --ink: #111111;
    --ink-soft: #1c1c1c;
    --rule: #d6d6d6;
    --paper: #ffffff;
    --shadow: rgba(0, 0, 0, 0.22);
  }
  * { margin: 0; padding: 0; box-sizing: border-box; }
  html, body {
    width: 1200px;
    height: 1000px;
    overflow: hidden;
    background: var(--canvas);
    font-family: "Lato", sans-serif;
  }
  .stage { position: relative; width: 1200px; height: 1000px; }
  .card {
    position: absolute;
    left: 254px;
    width: 693px;
    height: 396px;
    border-radius: 18px;
    box-shadow: 0 3px 6px var(--shadow);
    overflow: hidden;
  }
  .card--front { top: 78px; background: var(--card-light); color: var(--ink); }
  .card--back { top: 526px; background: var(--card-dark); color: var(--paper); }

  /* front: identity */
  .brand-front {
    position: absolute;
    left: 47px;
    top: 132px;
    display: flex;
    align-items: center;
    gap: 12px;
  }
  .brand-dot {
    width: 12px; height: 12px;
    border-radius: 50%;
    background: var(--ink);
    flex: none;
  }
  .brand-name {
    font-weight: 400;
    font-size: 21px;
    letter-spacing: 2.5px;
    line-height: 1.25;
    text-transform: uppercase;
    color: var(--ink);
  }
  .person {
    position: absolute;
    left: 47px;
    top: 198px;
  }
  .person-name {
    font-weight: 700;
    font-size: 30px;
    line-height: 36px;
    letter-spacing: 0.2px;
  }
  .person-title {
    font-weight: 400;
    font-size: 17px;
    line-height: 22px;
    margin-top: 4px;
    color: var(--ink-soft);
  }
  .contact-list {
    position: absolute;
    left: 47px;
    top: 280px;
    list-style: none;
  }
  .contact-item {
    display: flex;
    align-items: center;
    height: 25.5px;
    font-size: 15.5px;
    color: var(--ink-soft);
  }
  .contact-item--phone { font-size: 18px; }
  .contact-icon {
    width: 14px; height: 14px;
    margin-right: 10px;
    flex: none;
  }

  /* front: services */
  .services {
    position: absolute;
    left: 400px;
    top: 0;
    bottom: 0;
    width: 293px;
    padding-left: 36px;
    border-left: 1px solid var(--rule);
    display: flex;
    flex-direction: column;
    justify-content: center;
  }
  .services-list { list-style: none; }
  .service {
    display: flex;
    align-items: center;
    gap: 14px;
    height: 52px;
    font-size: 15px;
    font-weight: 700;
    letter-spacing: 0.8px;
    text-transform: uppercase;
    color: var(--ink);
  }
  .service-badge {
    width: 38px; height: 38px;
    border: 1.5px solid var(--ink);
    border-radius: 50%;
    display: flex;
    align-items: center;
    justify-content: center;
    flex: none;
  }
  .service-icon {
    width: 18px; height: 18px;
    fill: none;
    stroke: var(--ink);
    stroke-width: 1.6;
    stroke-linecap: round;
    stroke-linejoin: round;
  }

  /* back */
  .brand-back {
    position: absolute;
    left: 44px;
    bottom: 40px;
    display: flex;
    align-items: center;
    gap: 12px;
  }
  .brand-back .brand-dot { background: var(--paper); }
  .brand-back .brand-name {
    color: var(--paper);
    font-size: 18px;
    letter-spacing: 3px;
  }
</style>
</head>
<body>
<main class="stage">
  <section class="card card--front" aria-label="Card front">
    <div class="brand-front">
      <span class="brand-dot"></span>
      <span class="brand-name">Bright Harbor<br>Studios</span>
    </div>
    <div class="person">
      <h1 class="person-name">Desmond Whitfield</h1>
      <p class="person-title">Real Estate Media Specialist</p>
    </div>
    <ul class="contact-list">
      <li class="contact-item contact-item--phone">
        <svg class="contact-icon" viewBox="0 0 24 24" aria-hidden="true"><path fill="#111" d="M6.6 10.8a15.2 15.2 0 0 0 6.6 6.6l2.2-2.2a1 1 0 0 1 1-.25 11.4 11.4 0 0 0 3.6.57 1 1 0 0 1 1 1V20a1 1 0 0 1-1 1A17 17 0 0 1 3 4a1 1 0 0 1 1-1h3.5a1 1 0 0 1 1 1c0 1.25.2 2.45.57 3.57a1 1 0 0 1-.25 1z"/></svg>
        610-555-0187
      </li>
      <li class="contact-item">
        <svg class="contact-icon" viewBox="0 0 24 24" aria-hidden="true"><path fill="#111" d="M2 5h20v14H2z"/><path fill="none" stroke="#fff" stroke-width="1.8" d="M3 6l9 7 9-7"/></svg>
        desmond@brightharborstudios.com
      </li>
      <li class="contact-item">
        <svg class="contact-icon" viewBox="0 0 24 24" aria-hidden="true"><circle cx="12" cy="12" r="9.5" fill="none" stroke="#111" stroke-width="2"/><path fill="none" stroke="#111" stroke-width="1.6" d="M2.5 12h19M12 2.5c3 3 3 16 0 19M12 2.5c-3 3-3 16 0 19"/></svg>
        brightharborstudios.com
      </li>
    </ul>

    <aside class="services" aria-label="Services">
      <ul class="services-list">
        <li class="service">
          <span class="service-badge"><svg class="service-icon" viewBox="0 0 24 24" aria-hidden="true"><rect x="3" y="4" width="18" height="16" rx="2"/><circle cx="9" cy="9.5" r="1.8"/><path d="M3 17l5-5 4 4 3-3 6 6"/></svg></span>
          Real Estate Photography
        </li>
        <li class="service">
          <span class="service-badge"><svg class="service-icon" viewBox="0 0 24 24" aria-hidden="true"><rect x="2.5" y="6" width="13" height="12" rx="2"/><path d="M15.5 10.5l6-3.5v10l-6-3.5z"/></svg></span>
          Cinematic Video
        </li>
        <li class="service">
          <span class="service-badge"><svg class="service-icon" viewBox="0 0 24 24" aria-hidden="true"><rect x="9" y="9" width="6" height="6" rx="1"/><path d="M9 9L6 6M15 9l3-3M9 15l-3 3M15 15l3 3"/><circle cx="5" cy="5" r="2.5"/><circle cx="19" cy="5" r="2.5"/><circle cx="5" cy="19" r="2.5"/><circle cx="19" cy="19" r="2.5"/></svg></span>
          Drone
        </li>
        <li class="service">
          <span class="service-badge"><svg class="service-icon" viewBox="0 0 24 24" aria-hidden="true"><rect x="6" y="2.5" width="12" height="19" rx="2"/><path d="M10.5 9.5l4 2.5-4 2.5z"/></svg></span>
          Social Media Reels
        </li>
        <li class="service">
          <span class="service-badge"><svg class="service-icon" viewBox="0 0 24 24" aria-hidden="true"><rect x="3" y="3" width="18" height="18"/><path d="M12 3v7M12 14v7M3 12h6M15 12h6"/></svg></span>
          Floor Plans
        </li>
      </ul>
    </aside>
  </section>

  <section class="card card--back" aria-label="Card back">
    <div class="brand-back">
      <span class="brand-dot"></span>
      <span class="brand-name">Bright Harbor Studios</span>
    </div>
  </section>
</main>
</body>
</html>
```